Professional and creative business card design for recruiting service providers

Our company supports German medium-sized companies in filling vacancies promptly. For this we use social media marketing and bring our customers into the visibility.

We want a professional but also creative design for our business cards.

Please look at lindqvar-staff.de to get an impression of our CI.

Target Market(s)

Small and medium-sized companies in Germany from the industry

Industry/Entity Type

Industrie, Handwerk

Contact Information for Business Card

Name, Position, Telefonnummer, Email, Website

Colors
EE7325
F08F49
F5BC92
FAE3D3
FDF4ED

Requirements
Must have
• A picture of the employee and in the style of www.lindqvar-staff.de

```html
<!DOCTYPE html>
<html lang="de">
<head>
<meta charset="utf-8">
<title>Lindqvar &amp; Staff – Visitenkarte</title>
<link rel="stylesheet" href="https://fonts.googleapis.com/css2?family=Montserrat:wght@400;500;600;700&display=swap">
<style>
  :root {
    --stage: #1b1b1c;
    --card: #262627;
    --orange: #ee7325;
    --white: #ffffff;
    --text-light: #f2f2f2;
    --photo-dark: #1e2029;
    --photo-mid: #3a3c47;
  }
  * { margin: 0; padding: 0; box-sizing: border-box; }
  html, body {
    width: 1200px; height: 1059px; overflow: hidden;
    background: var(--stage);
    font-family: "Montserrat", sans-serif;
  }
  .canvas { position: relative; width: 1200px; height: 1059px; }

  .card {
    position: absolute;
    background: var(--card);
    border-radius: 22px;
    overflow: hidden;
  }
  .card--front { left: 257px; top: 89px; width: 687px; height: 390px; }
  .card--back  { left: 254px; top: 547px; width: 693px; height: 393px; }

  .front-shapes { position: absolute; inset: 0; }

  .portrait {
    position: absolute; left: 380px; top: 10px; width: 555px; height: 380px;
    width: 300px;
    border-radius: 90px 90px 8px 8px;
    background: linear-gradient(180deg, var(--photo-mid) 0%, var(--photo-dark) 55%, #15161c 100%);
  }

  .brand {
    position: absolute; left: 28px; top: 88px;
    display: flex; align-items: center; gap: 14px;
  }
  .brand__square { width: 40px; height: 40px; background: var(--orange); }
  .brand__name {
    color: var(--white); font-weight: 700; font-size: 20px;
    line-height: 23px; letter-spacing: 1.6px; text-transform: uppercase;
  }

  .person__bar {
    position: absolute; left: 0; top: 214px; width: 14px; height: 34px;
    background: var(--orange);
  }
  .person__name {
    position: absolute; left: 28px; top: 208px;
    color: var(--orange); font-weight: 700; font-size: 21px; letter-spacing: 0.6px;
  }
  .person__role {
    position: absolute; left: 28px; top: 233px;
    color: var(--text-light); font-weight: 600; font-size: 15px; letter-spacing: 0.3px;
  }

  .contact { position: absolute; left: 28px; top: 280px; list-style: none; }
  .contact__item {
    display: flex; align-items: center; gap: 6px;
    height: 27px; color: var(--text-light); font-size: 15.5px; font-weight: 400; letter-spacing: 0.4px;
  }
  .contact__icon { width: 12px; height: 12px; flex: none; }

  .back-name {
    position: absolute; right: 37px; top: 248px;
    color: var(--white); font-weight: 700; font-size: 50px; line-height: 51px;
    letter-spacing: 3.5px; text-align: left; text-transform: uppercase;
  }
</style>
</head>
<body>
<main class="canvas">

  <section class="card card--front">
    <svg class="front-shapes" width="687" height="390" viewBox="0 0 687 390" aria-hidden="true">
      <path d="M230 0 H687 V297 Q560 312 396 282 Q262 200 230 0 Z" fill="var(--white)"/>
      <path d="M243 0 Q272 196 398 280" fill="none" stroke="var(--orange)" stroke-width="18"/>
    </svg>

    <div class="portrait" role="img" aria-label="Porträtfoto des Gründers im dunklen Sakko am Schreibtisch"></div>

    <div class="brand">
      <span class="brand__square"></span>
      <span class="brand__name">Lindqvar<br>&amp; Staff</span>
    </div>

    <span class="person__bar"></span>
    <h1 class="person__name">JONAS LINDQVAR</h1>
    <p class="person__role">Gründer</p>

    <ul class="contact">
      <li class="contact__item">
        <svg class="contact__icon" viewBox="0 0 24 24"><path fill="var(--orange)" d="M6.6 10.8a15.1 15.1 0 0 0 6.6 6.6l2.2-2.2c.3-.3.7-.4 1-.2 1.1.4 2.3.6 3.6.6.6 0 1 .4 1 1V20c0 .6-.4 1-1 1A17 17 0 0 1 3 4c0-.6.4-1 1-1h3.5c.6 0 1 .4 1 1 0 1.3.2 2.5.6 3.6.1.3 0 .7-.2 1z"/></svg>
        (123) 456 7890
      </li>
      <li class="contact__item">
        <svg class="contact__icon" viewBox="0 0 24 24"><path fill="var(--orange)" d="M2 5h20v14H2z"/><path fill="none" stroke="var(--card)" stroke-width="2" d="M2 6l10 7 10-7"/></svg>
        info@lindqvar-staff.de
      </li>
      <li class="contact__item">
        <svg class="contact__icon" viewBox="0 0 24 24"><g fill="none" stroke="var(--orange)" stroke-width="2"><circle cx="12" cy="12" r="10"/><ellipse cx="12" cy="12" rx="4.5" ry="10"/><path d="M2 12h20M4 7h16M4 17h16"/></g></svg>
        www.lindqvar-staff.de
      </li>
    </ul>
  </section>

  <section class="card card--back">
    <h2 class="back-name">Lindqvar<br>&amp; Staff</h2>
  </section>

</main>
</body>
</html>
```